Letterhead for a German Distribution/Manufacturing Company

We need a professional Letterhead in a unique Design.
not to playful.
The Letterhead has to show show that we are a international company with headquater in Germany.
all details like adress, Vat Tax Number, Bank Accout, Eori, email, Company number has to be on the Letterhead.
for example use: VAT TAX DE5470318 Bank Account: Kestrel Bank IBAN DE412058731ß204683 Swift: MORV0417352 EORI 3150428697 Company Number: HRB 51806 Adress: VOLMINTA UG Ahornweg 7 Postal Code 06384 City Lindenfeld Country: Germany Email: info@volminta-example.com
the design can be colored but doesnt have to be
Industry/Entity Type
Manufacturing and international distribution
Requirements
Must have
- show that we are a international company with headquater in Germany. our company infos and logo

```html
<!DOCTYPE html>
<html lang="en">
<head>
<meta charset="utf-8">
<title>VOLMINTA Letterhead</title>
<link href="https://fonts.googleapis.com/css2?family=Saira:wght@300;400;600&display=swap" rel="stylesheet">
<style>
  :root {
    --paper: #ffffff;
    --band-dark: #737371;
    --band-light: #b3b3b3;
    --ink: #2b2b2b;
    --ink-soft: #3a3a3a;
    --leader: #b8b8b8;
  }
  * { margin: 0; padding: 0; box-sizing: border-box; }
  html, body { width: 919px; height: 1200px; overflow: hidden; background: var(--paper); }
  .letterhead {
    position: relative;
    width: 919px;
    height: 1200px;
    background: var(--paper);
    font-family: "Saira", Arial, sans-serif;
    color: var(--ink);
  }
  .bar { position: absolute; }
  .bar--dark { background: var(--band-dark); }
  .bar--light { background: var(--band-light); }

  .brand {
    position: absolute;
    left: 63px;
    top: 74px;
    display: flex;
    align-items: center;
    gap: 14px;
  }
  .brand__dot {
    width: 44px; height: 44px;
    border-radius: 50%;
    background: var(--ink);
  }
  .brand__name {
    font-size: 37px;
    font-weight: 400;
    letter-spacing: 0.5px;
    color: var(--ink);
    line-height: 1;
  }

  .contact {
    position: absolute;
    right: 34px;
    top: 50px;
    text-align: right;
    font-size: 15px;
    font-weight: 300;
    font-style: normal;
    line-height: 24.7px;
    letter-spacing: 0.3px;
    color: var(--ink-soft);
  }
  .label { font-weight: 600; color: var(--ink); }

  .leader {
    position: absolute;
    height: 1px;
    background: var(--leader);
  }

  .company-details {
    position: absolute;
    left: 40px;
    top: 1050px;
    font-size: 15px;
    font-weight: 300;
    line-height: 25px;
    letter-spacing: 0.3px;
    color: var(--ink-soft);
    list-style: none;
  }
</style>
</head>
<body>
<main class="letterhead">
  <div class="bar bar--dark" style="left:0;top:16px;width:215px;height:7px;"></div>
  <div class="bar bar--light" style="left:225px;top:0;width:7px;height:39px;"></div>
  <div class="bar bar--light" style="left:240px;top:0;width:7px;height:39px;"></div>
  <div class="bar bar--dark" style="left:254px;top:0;width:665px;height:39px;"></div>

  <div class="brand">
    <span class="brand__dot"></span>
    <span class="brand__name">VOLMINTA</span>
  </div>

  <address class="contact">
    <div><span class="label">Address :</span> VOLMINTA UG Ahornweg</div>
    <div>7 Postal Code 06384</div>
    <div>City Lindenfeld Country : Germany</div>
    <div><span class="label">Email :</span> info@volminta-example.com</div>
  </address>
  <div class="leader" style="left:889px;top:62px;width:30px;"></div>
  <div class="leader" style="left:889px;top:136px;width:30px;"></div>

  <ul class="company-details">
    <li><span class="label">VAT TAX :</span>&nbsp; DE5470318</li>
    <li><span class="label">Bank Account :</span> Kestrel Bank IBAN DE412058731ß204683</li>
    <li><span class="label">Swift :</span> MORV0417352 EORI 3150428697</li>
    <li><span class="label">Company Number :</span> HRB 51806</li>
  </ul>
  <div class="leader" style="left:0;top:1063px;width:30px;"></div>
  <div class="leader" style="left:0;top:1088px;width:30px;"></div>
  <div class="leader" style="left:0;top:1113px;width:30px;"></div>
  <div class="leader" style="left:0;top:1138px;width:30px;"></div>

  <div class="bar bar--dark" style="left:0;top:1161px;width:665px;height:39px;"></div>
  <div class="bar bar--light" style="left:672px;top:1161px;width:7px;height:39px;"></div>
  <div class="bar bar--light" style="left:688px;top:1161px;width:7px;height:39px;"></div>
  <div class="bar bar--dark" style="left:705px;top:1177px;width:214px;height:7px;"></div>
</main>
</body>
</html>
```